Website for Torvel Capital - investment banking firm

We have a corporate identity (thanks to Ravinka/31842) and want to extend that into a website design.  See the attached zipped files.
We have software folks in-house to do the coding.
See the attached Project Brief & Notes for more details.  Don't worry about the actual text - lorem ipsum will be fine.
The server will be Apache.
Thank you!
Desmond

Industry/Entity Type
Investment

```html
<!DOCTYPE html>
<html lang="en">
<head>
<meta charset="utf-8">
<title>Torvel Capital</title>
<link rel="stylesheet" href="https://fonts.googleapis.com/css2?family=Open+Sans:wght@400;600;700&family=Ubuntu:wght@400;700&family=Roboto+Condensed:wght@400&display=swap">
<style>
:root{
  --blue:#2d62b0;
  --blue-dark:#1f4c92;
  --navy:#1b3a66;
  --icon:#1f4a8c;
  --text-grey:#6d6d6d;
  --light:#eeeeee;
  --header-bg:#f0f0f0;
  --white:#ffffff;
  --ink:#222222;
}
*{margin:0;padding:0;box-sizing:border-box}
html,body{width:1200px;height:2375px;overflow:hidden}
body{position:relative;font-family:"Open Sans",Arial,sans-serif;background:var(--white);color:var(--ink)}
.abs{position:absolute}

/* header */
.site-header{left:0;top:0;width:1200px;height:126px;background:var(--header-bg)}
.brand{left:108px;top:40px;display:flex;align-items:center;gap:14px}
.brand-mark{width:44px;height:44px;background:var(--navy)}
.brand-name{font-family:"Open Sans",sans-serif;font-weight:600;font-size:29px;color:var(--navy);letter-spacing:.5px}
.main-nav{left:540px;top:58px;display:flex;gap:0;font-family:"Roboto Condensed",Arial,sans-serif;font-size:16px;color:#333}
.main-nav a{text-decoration:none;color:#333;margin-right:24px}
.main-nav a.active{color:var(--blue-dark)}
.main-nav a:nth-child(4){margin-right:36px}

/* hero */
.hero{left:0;top:126px;width:1200px;height:468px;background:linear-gradient(90deg,#c9d9ee 0%,#a8c2e4 35%,#dbe6f2 60%,#b6cbe6 100%)}
.hero-caption{left:108px;top:272px;width:418px;height:136px;background:rgba(255,255,255,.85);padding:14px 0 0 28px;font-family:"Ubuntu",sans-serif;color:#111}
.hero-caption .line1{font-size:31px;line-height:38px}
.hero-caption .big{font-size:58px;font-weight:700;line-height:62px}
.hero-caption .small{font-size:31px}
.hero-arrow{top:307px;width:57px;height:63px;background:#000;display:flex;align-items:center;justify-content:center}

/* welcome */
.welcome{left:0;top:594px;width:1200px;height:158px;background:linear-gradient(180deg,var(--blue) 0%,var(--blue-dark) 100%);color:var(--white);padding:32px 0 0 108px}
.welcome h1{font-weight:400;font-size:25px;margin-bottom:16px}
.welcome p{font-size:16px}

/* services */
.service{top:817px;width:250px;text-align:center}
.service-icon{width:63px;height:63px;border-radius:50%;background:var(--icon);margin:0 auto 26px;display:flex;align-items:center;justify-content:center}
.service h2{font-weight:400;font-size:19px;color:var(--blue-dark);margin-bottom:16px;white-space:nowrap}
.service p{font-size:14.5px;line-height:25px;color:var(--text-grey);height:100px}
.service .more{display:block;font-size:14.5px;color:var(--blue-dark);text-decoration:none;margin-top:4px}

/* who we are */
.who{left:0;top:1150px;width:1200px;height:306px;background:linear-gradient(180deg,var(--blue) 0%,var(--blue-dark) 100%);color:var(--white)}
.who h2{left:108px;top:38px;font-weight:400;font-size:25px}
.who p{left:108px;top:98px;width:570px;font-size:16.5px;line-height:31px}
.who-visual{left:677px;top:21px;width:371px;height:266px;background:linear-gradient(180deg,#3a3a3a 0%,#b8902e 40%,#d4a93c 70%,#2b2b2b 100%);border-radius:6px}

/* process */
.process{left:0;top:1456px;width:1200px;height:364px;background:var(--light)}
.world-map{left:111px;top:111px;width:380px;height:183px;background:linear-gradient(90deg,#4a4a4a,#3a3a3a);border-radius:40px}
.process h2{left:526px;top:60px;font-weight:400;font-size:22px;color:var(--blue-dark)}
.process p{left:526px;top:110px;width:570px;font-size:16.5px;line-height:31.5px;color:#555}

/* clients */
.clients{left:0;top:1820px;width:1200px;height:159px;background:#f7f7f7}
.clients h2{left:108px;top:34px;font-weight:400;font-size:20px;color:var(--blue-dark)}
.client-name{top:76px;font-family:"Open Sans",sans-serif;font-weight:700;font-size:42px;letter-spacing:-.5px}

/* footer */
.site-footer{left:0;top:1979px;width:1200px;height:301px;background:linear-gradient(180deg,var(--blue) 0%,var(--blue-dark) 100%);color:var(--white)}
.site-footer h3{font-weight:400;font-size:18px}
.contact{left:112px;top:49px;width:240px}
.contact p{font-size:12px;line-height:19px;margin-top:18px}
.contact .detail{margin-top:18px}
.contact .detail + .detail{margin-top:10px}
.socials{display:flex;gap:6px;margin-top:26px}
.socials span{width:36px;height:36px;border-radius:50%;background:var(--white)}
.news{left:438px;top:49px;width:380px}
.news-item{display:flex;gap:18px;margin-top:22px}
.news-item:first-of-type{margin-top:26px}
.news-thumb{width:66px;height:50px;border:3px solid #4a7cc6;background:linear-gradient(135deg,#8a8f96,#c9ccd0);flex:none}
.news-item p{font-size:13px;font-weight:600;line-height:21px}
.news-item small{display:block;font-size:11px;font-weight:400;margin-top:4px}
.newsletter{left:858px;top:44px;width:240px}
.mail-input{width:206px;height:40px;background:var(--white);margin-top:18px;color:#555;font-size:13px;padding:11px 0 0 14px}
.subscribe{width:124px;height:41px;background:var(--navy);margin-top:22px;font-size:14px;text-align:center;line-height:41px}
.copyright{left:0;top:2280px;width:1200px;height:95px;background:var(--blue-dark);color:var(--white);font-size:12.5px;text-align:center;padding-top:43px}
</style>
</head>
<body>

<header class="site-header abs">
  <div class="brand abs"><span class="brand-mark"></span><span class="brand-name">TorvelCapital</span></div>
  <nav class="main-nav abs">
    <a class="active" href="#">Home</a><a href="#">About</a><a href="#">Services</a><a href="#">Current Engagements</a><a href="#">Completed Transactions</a>
  </nav>
</header>

<section class="hero abs" role="img" aria-label="Photo of a smiling businesswoman in a dark suit presenting with an open hand in a bright blurred office"></section>
<div class="hero-caption abs">
  <div class="line1">Global Investment</div>
  <div><span class="big">Banking</span> <span class="small">Services</span></div>
</div>
<div class="hero-arrow abs" style="left:0">
  <svg width="16" height="26" viewBox="0 0 16 26"><path d="M13 2L3 13l10 11" fill="none" stroke="#fff" stroke-width="2"/></svg>
</div>
<div class="hero-arrow abs" style="left:1148px;width:52px">
  <svg width="16" height="26" viewBox="0 0 16 26"><path d="M3 2l10 11L3 24" fill="none" stroke="#fff" stroke-width="2"/></svg>
</div>

<section class="welcome abs">
  <h1>Welcome to torvelcapital ! A World Leading Company</h1>
  <p>in research and development, trade, finance, inovation of future technology with over 30 years of experience.</p>
</section>

<div class="service abs" style="left:95px">
  <div class="service-icon"><svg width="24" height="30" viewBox="0 0 24 30"><rect x="3" y="2" width="18" height="26" rx="2" fill="#fff"/></svg></div>
  <h2>Strategic AdvisoryServices</h2>
  <p>We assist corporate clients and private equity groups to identify opportunities for growth by acquisition</p>
  <a class="more" href="#">Read More...</a>
</div>
<div class="service abs" style="left:344px">
  <div class="service-icon"><svg width="30" height="26" viewBox="0 0 30 26"><circle cx="9" cy="6" r="4" fill="#fff"/><circle cx="21" cy="6" r="4" fill="#fff"/><rect x="3" y="12" width="24" height="12" rx="3" fill="#fff"/></svg></div>
  <h2>Current Engagements</h2>
  <p>Some companies have exciting growth prospects but lack the financial base to capitalize on the opportunities</p>
  <a class="more" href="#">Read More...</a>
</div>
<div class="service abs" style="left:594px">
  <div class="service-icon"><svg width="30" height="22" viewBox="0 0 30 22"><path d="M6 2h22l-4 18H2z" fill="#fff"/></svg></div>
  <h2>Completed Transactions</h2>
  <p>We identify the appropriate buyer targets, work alongside the owner and his professional advisors to develop</p>
  <a class="more" href="#">Read More...</a>
</div>
<div class="service abs" style="left:845px">
  <div class="service-icon"><svg width="34" height="24" viewBox="0 0 34 24"><circle cx="8" cy="7" r="4" fill="#fff"/><circle cx="17" cy="6" r="5" fill="#fff"/><circle cx="26" cy="7" r="4" fill="#fff"/><rect x="2" y="13" width="30" height="10" rx="4" fill="#fff"/></svg></div>
  <h2>Regulatory Compliance</h2>
  <p>We identify the appropriate buyer targets, work alongside the owner and his professional advisors to develop</p>
  <a class="more" href="#">Read More...</a>
</div>

<section class="who abs">
  <h2 class="abs">Who We Are</h2>
  <p class="abs">Once we have your acquisition parameters, we feed these into our soft-ware to create an initial target list. The criteria used to create this list can include geography, revenue targets, earning targets, margins, shareholder structure, etc.</p>
  <div class="who-visual abs" role="img" aria-label="Illustration of a laptop showing banknotes and a photo frame on its screen"></div>
</section>

<section class="process abs">
  <div class="world-map abs" role="img" aria-label="Dark grey world map"></div>
  <h2 class="abs">Our Process</h2>
  <p class="abs">When our software has identified a qualified list, Torvel will reach out to prospective sellers. We will gather basic information during this process. At this time, we will keep all information within our firm until we have approval by the potential seller to reach out directly to the buyer.</p>
</section>

<section class="clients abs">
  <h2 class="abs">Our Clients</h2>
  <span class="client-name abs" style="left:106px;color:#f04a2a">BRIGHTLANE</span>
  <span class="client-name abs" style="left:452px;color:#2b2b2b">STUDIOHALL</span>
  <span class="client-name abs" style="left:790px;color:#f2b90f">AmberWorks</span>
</section>

<footer class="site-footer abs">
  <div class="contact abs">
    <h3>Contact Info</h3>
    <p>Lorem ipsum dolor sit amet, consectetur adipisicing elit, sed do eiusmod tempor</p>
    <p class="detail">(555) 0142 318420</p>
    <p class="detail">info@torvelmail.com</p>
    <div class="socials"><span></span><span></span><span></span><span></span></div>
  </div>
  <div class="news abs">
    <h3>Latest News</h3>
    <div class="news-item">
      <div class="news-thumb" role="img" aria-label="News thumbnail photo"></div>
      <p>Lorem ipsum dolor sit amet, consectetur adipisicing elit,<small>july 7, 2014</small></p>
    </div>
    <div class="news-item">
      <div class="news-thumb" role="img" aria-label="News thumbnail photo"></div>
      <p>Lorem ipsum dolor sit amet, consectetur adipisicing elit,<small>july 7, 2014</small></p>
    </div>
  </div>
  <div class="newsletter abs">
    <h3>Subscribe to our Newsletter</h3>
    <div class="mail-input">Enter Your Mail Id</div>
    <div class="subscribe">Subscribe</div>
  </div>
</footer>
<div class="copyright abs">© Copyright 2014 &nbsp;torvelcapital.com . &nbsp;All Rights Reserved</div>

</body>
</html>
```